Web and Logo Design for eCommerce site

We're launching a sister brand and require a full design for the site.

The site must have an established feel and appeal to corporate and institutional buyers.
Updates

Just a note about the wireframe design:

The Search & Rescue / Coast Guard / NVDK, etc. in the header area aren't buttons or menu items, but rather just info (along the lines of a tagline).  Sort of a "who we serve" sort of thing.

Worth noting is that it's specifically geared towards LARGE BUYERS.  For example, a police force buying 200 headlamps and 85 pairs of gloves.  So they'll register + sign in and then add a bunch of items to a RFQ.

Aim for a professional, masculine design.

Target Market(s)

We will be selling outdoor gear to the military, law enforcement, fire and rescue and first responders.

Requirements
Must have
• We require:
- Logo (vector based)

Site:
- template page
* main site template, re-skinned version of our current site
* horizontal drop-down menu
- product listings page
* thumbnail view of products
- product details page
* including elements such as product image, color/size selector, descriptions and specs (again, based loosely on our current website)
- account management page
* illustrating basic data entry styles for text box, buttons, grid, etc.

The site needs to be given a responsive design, so 2 versions of each design should be presented for desktop + mobile views.

Additional funds are available if the designer is able to fully implement the designs into a responsive framework such as bootstrap.

Nice to have
• Clean, professional design similar to:

http://military.trailvexagear.com/gov/accessories/gloves.html

http://leaf.ombrivo.com/ProductFind.aspx?language=EN&category=Hardshell&subcat=Waterproof_Jackets

```html
<!DOCTYPE html>
<html lang="en">
<head>
<meta charset="utf-8">
<title>Valtrek – Canada Outdoor Pro Supply</title>
<link href="https://fonts.googleapis.com/css2?family=Open+Sans:wght@400;600;700&family=Ubuntu:wght@300;400;700&display=swap" rel="stylesheet">
<style>
:root{
  --blue:#1e8ee8;
  --blue-light:#5cb3f6;
  --dark:#3a3a3a;
  --text:#333;
  --muted:#8a8a8a;
  --page:#f4f4f4;
  --white:#fff;
}
*{margin:0;padding:0;box-sizing:border-box}
html,body{width:724px;height:1200px;overflow:hidden}
body{font-family:"Open Sans",Arial,sans-serif;color:var(--text);background:var(--page)}
.page{position:relative;width:724px;height:1200px;overflow:hidden}
.backdrop{position:absolute;left:0;top:0;width:724px;height:995px;
  background:linear-gradient(180deg,#9a9a9a 0%,#c9c9c9 12%,#e4e4e4 30%,#f1f1f1 50%,var(--page) 70%)}
.abs{position:absolute}
.brand{font-family:"Ubuntu",sans-serif;font-weight:700;color:var(--blue);line-height:1}
.brand-sub{font-size:9px;color:#222}
.tagline{right:73px;top:32px;text-align:right;font-size:10px;line-height:14.5px;color:#111}
.login{left:602px;top:66px;width:49px;height:15px;background:var(--blue);color:var(--white);font-size:8.5px;font-weight:700;text-align:center;line-height:15px}
.serve{left:72px;top:86px;width:579px;height:22px;background:var(--dark);color:#c8c8c8;font-size:8px;text-align:center;line-height:22px;word-spacing:1px}
.serve span{margin:0 5px}
.nav{left:72px;top:108px;width:579px;height:37px;background:linear-gradient(180deg,var(--blue-light),#2f95ec);display:flex;list-style:none}
.nav li{color:var(--white);font-size:8.5px;font-weight:700;line-height:37px;padding:0 9.5px;border-right:1px solid rgba(255,255,255,.35)}
.nav li:last-child{border:none}
.hero{left:72px;top:154px;width:579px;height:260px;border-radius:2px;
  background:radial-gradient(ellipse at 40% 30%,#e9d3a6 0%,#b98d58 25%,#6d5a48 55%,#2e2a28 100%)}
.hero-title{left:342px;top:260px;font-family:"Ubuntu",sans-serif;font-size:22px;color:#3aa1f2}
.hero-sub{left:342px;top:289px;font-family:"Ubuntu",sans-serif;font-weight:300;font-size:13.5px;color:#eee}
.products-bar{left:72px;top:427px;width:579px;height:34px;background:var(--dark);color:var(--white)}
.products-bar h2{position:absolute;left:11px;top:10px;font-size:11px;font-weight:700;letter-spacing:.2px}
.filter{position:absolute;left:422px;top:7px;width:151px;height:21px;background:var(--white);border-radius:2px;font-size:8px;color:#aaa;padding:5px 8px}
.filter i{position:absolute;right:6px;top:5px;width:10px;height:10px;border:1px solid #999}
.grid{left:78px;top:468px;width:570px;display:grid;grid-template-columns:repeat(4,134px);column-gap:11px;row-gap:0}
.card{height:202px}
.card-photo{height:94px;background:var(--white);border:1px solid #e2e2e2;padding:10px}
.card-photo div{width:100%;height:100%;border-radius:3px}
.card h3{font-size:8.5px;font-weight:700;margin-top:10px;color:#333}
.card p{font-size:6.5px;color:var(--muted);line-height:14.5px;margin-top:3px}
.price{font-size:17.5px;color:#222;margin-top:1px;line-height:22px}
.add{display:inline-block;margin-top:3px;width:57px;height:19px;background:var(--blue);color:var(--white);font-size:7px;font-weight:700;text-align:center;line-height:19px}
.perks{left:72px;top:896px;width:579px;height:80px;font-family:"Ubuntu",sans-serif;color:#888}
.perk{position:absolute;text-align:center;line-height:1.05}
.perk b{color:var(--blue);font-weight:700}
.divider{width:1px;height:80px;background:linear-gradient(180deg,transparent,#ccc,transparent)}
.footer{left:0;top:995px;width:724px;height:205px;background:var(--dark);color:#ddd}
.footer h4{position:absolute;top:22px;font-size:8.5px;font-weight:700;color:var(--white)}
.links{position:absolute;top:47px;list-style:none;font-size:7px;line-height:14.4px}
.newsletter-text{position:absolute;left:415px;top:46px;width:140px;font-size:7px;line-height:12px}
.field{position:absolute;left:415px;width:134px;height:16px;background:#f2f2f2;border:1px solid #ccc}
.subscribe{position:absolute;left:494px;top:123px;width:55px;height:16px;border-radius:8px;background:#5a5a5a;color:var(--white);font-size:7px;font-weight:700;text-align:center;line-height:16px}
.social{position:absolute;left:562px;width:79px;height:16px;font-size:6.5px;line-height:16px;text-align:right}
.social i{position:absolute;left:0;top:0;width:16px;height:16px;border-radius:50%;background:#d8d8d8}
.copyright{position:absolute;left:0;width:724px;top:181px;text-align:center;font-size:7.5px}
</style>
</head>
<body>
<div class="page">
  <div class="backdrop abs" role="img" aria-label="Snowy mountain slopes with a ski lift, in black and white"></div>

  <header>
    <div class="abs" style="left:72px;top:38px">
      <div class="brand" style="font-size:28px">Valtrek</div>
      <div class="brand-sub" style="margin-top:3px">Canada Outdoor Pro Supply</div>
    </div>
    <div class="abs tagline">Great Outdoor Gear For<br>Canada’s First Responder’s</div>
    <div class="abs login">LOGIN</div>
    <div class="abs serve">Search &amp; Rescue<span>**</span>Coast Guard<span>**</span>NVDK<span>**</span>Fire<span>**</span>Military<span>**</span>Law Enforcement</div>
    <ul class="abs nav">
      <li>Rescue Gear</li><li>Footwear</li><li>Clothing</li><li>Tents,mats ,Sleeping&nbsp;Bags</li><li>Camping Gear</li><li>Snow Sports</li><li>Brands</li>
    </ul>
  </header>

  <section>
    <div class="abs hero" role="img" aria-label="Hiker with a backpack raising his arms on a rocky summit at sunset"></div>
    <div class="abs hero-title">Valtrek</div>
    <div class="abs hero-sub">Cananda Outdoor Pro Supply</div>
    <svg class="abs" style="left:88px;top:268px" width="28" height="28" viewBox="0 0 28 28"><circle cx="14" cy="14" r="14" fill="rgba(255,255,255,.85)"/><path d="M16 8l-6 6 6 6" fill="none" stroke="#555" stroke-width="2.2"/></svg>
    <svg class="abs" style="left:609px;top:268px" width="28" height="28" viewBox="0 0 28 28"><circle cx="14" cy="14" r="14" fill="rgba(255,255,255,.85)"/><path d="M12 8l6 6-6 6" fill="none" stroke="#555" stroke-width="2.2"/></svg>
  </section>

  <section>
    <div class="abs products-bar">
      <h2>OUR PRODUCTS</h2>
      <div class="filter">All<i></i></div>
    </div>
    <div class="abs grid">
      <article class="card"><div class="card-photo"><div role="img" aria-label="Ski goggles" style="background:linear-gradient(90deg,#fff,#8fa0d8,#c86fb8,#fff)"></div></div><h3>Harwick Camp Axe</h3><p>Lorem Ipsum is simply dummy text of<br>the printing and typesetting</p><div class="price">$ 189.00</div><span class="add">ADD TO CART</span></article>
      <article class="card"><div class="card-photo"><div role="img" aria-label="Climbing harness" style="background:linear-gradient(180deg,#fff,#d25a5a 40%,#333 70%,#fff)"></div></div><h3>Harwick Camp Axe</h3><p>Lorem Ipsum is simply dummy text of<br>the printing and typesetting</p><div class="price">$ 189.00</div><span class="add">ADD TO CART</span></article>
      <article class="card"><div class="card-photo"><div role="img" aria-label="Yellow and black backpack" style="background:linear-gradient(90deg,#fff 25%,#e8c93a 40%,#2b2b2b 60%,#fff 75%)"></div></div><h3>Harwick Camp Axe</h3><p>Lorem Ipsum is simply dummy text of<br>the printing and typesetting</p><div class="price">$ 189.00</div><span class="add">ADD TO CART</span></article>
      <article class="card"><div class="card-photo"><div role="img" aria-label="Camp axe" style="background:linear-gradient(160deg,#fff 30%,#9a9a9a 45%,#222 60%,#fff 75%)"></div></div><h3>Harwick Camp Axe</h3><p>Lorem Ipsum is simply dummy text of<br>the printing and typesetting</p><div class="price">$ 189.00</div><span class="add">ADD TO CART</span></article>
      <article class="card"><div class="card-photo"><div role="img" aria-label="Tan tactical backpack" style="background:radial-gradient(circle,#a88c5c 0%,#b79c6c 40%,#fff 70%)"></div></div><h3>Harwick Camp Axe</h3><p>Lorem Ipsum is simply dummy text of<br>the printing and typesetting</p><div class="price">$ 189.00</div><span class="add">ADD TO CART</span></article>
      <article class="card"><div class="card-photo"><div role="img" aria-label="Green ski boot" style="background:radial-gradient(circle,#9ccc2a 0%,#444 40%,#fff 65%)"></div></div><h3>Harwick Camp Axe</h3><p>Lorem Ipsum is simply dummy text of<br>the printing and typesetting</p><div class="price">$ 189.00</div><span class="add">ADD TO CART</span></article>
      <article class="card"><div class="card-photo"><div role="img" aria-label="Black snow helmet" style="background:radial-gradient(circle,#1c1c1c 0%,#2a2a2a 40%,#fff 62%)"></div></div><h3>Harwick Camp Axe</h3><p>Lorem Ipsum is simply dummy text of<br>the printing and typesetting</p><div class="price">$ 189.00</div><span class="add">ADD TO CART</span></article>
      <article class="card"><div class="card-photo"><div role="img" aria-label="Blue dome tent" style="background:radial-gradient(ellipse,#2e4f8f 0%,#5a6fa8 40%,#fff 68%)"></div></div><h3>Harwick Camp Axe</h3><p>Lorem Ipsum is simply dummy text of<br>the printing and typesetting</p><div class="price">$ 189.00</div><span class="add">ADD TO CART</span></article>
    </div>
  </section>

  <section class="abs perks">
    <div class="perk" style="left:26px;top:24px;font-size:22px"><b>Free</b> Shipping</div>
    <div class="divider abs" style="left:210px;top:0"></div>
    <div class="perk" style="left:242px;top:18px;width:120px;font-size:22px"><b>365</b><br>Guaranteed</div>
    <div class="divider abs" style="left:381px;top:0"></div>
    <div class="perk" style="left:412px;top:18px;width:140px;font-size:22px"><b>30 days</b><br>Free Returns</div>
  </section>

  <footer class="abs footer">
    <div class="abs" style="left:78px;top:50px">
      <div class="brand" style="font-size:28px">Valtrek</div>
      <div class="brand-sub" style="color:#ddd;margin-top:3px">Canada Outdoor Pro Supply</div>
    </div>
    <h4 style="left:223px">Quick Links</h4>
    <ul class="links" style="left:223px"><li>Rescue Gear</li><li>Footwear</li><li>Clothing</li><li>Tents,mats ,Sleeping</li><li>Bags</li><li>Camping Gear</li><li>Snow Sports</li><li>Brands</li></ul>
    <h4 style="left:322px">Support Links</h4>
    <ul class="links" style="left:322px"><li>Legal Notice</li><li>Privacy Policy</li><li>Terms &amp; Conditions</li><li>Help</li></ul>
    <h4 style="left:415px">Newsletter SignUp</h4>
    <p class="newsletter-text">Sign-up for our daily emails by entering your information below:</p>
    <div class="field" style="top:76px"></div>
    <div class="field" style="top:102px"></div>
    <div class="subscribe">Subscribe</div>
    <h4 style="left:562px">Connect With Us</h4>
    <div class="social" style="top:47px"><i></i>Tweetline</div>
    <div class="social" style="top:70px"><i></i>Friendspace</div>
    <div class="social" style="top:93px"><i></i>Proflink</div>
    <p class="copyright">Copyright ©2013 Company name &nbsp; - All rights reserved</p>
  </footer>
</div>
</body>
</html>
```